Oil Field Service company needs professional business cards

Looking to clean up our current company business cards and look a little more professional. Brenwick Casing Services is a US based company that services the oil field. We deal with engineers, managers and oil rigs....................................................................................................................................................................................................................................................................................................................................................................................................

Target Market(s)

Oil and Gas professionals

Industry/Entity Type

Oil And Gas

Contact Information for Business Card

See attached photo as example

Font styles to use
Sans Serif

Colors
ec1f27

Requirements
Must have
• Company Logo, Name, Title, Cell, Office, Fax, Email.
• See attached photo
Nice to have
• External CRT, Internal CRT, Casing Crews, Torque Turn, Laydown Machine
Should not have
• Do not introduce any new pictures and keep it professional looking

```html
<!DOCTYPE html>
<html lang="en">
<head>
<meta charset="utf-8">
<title>Brenwick Casing Services – Business Card</title>
<link rel="stylesheet" href="https://fonts.googleapis.com/css2?family=Oswald:wght@300;400;600&family=Roboto:wght@400;700&display=swap">
<style>
  :root {
    --brand-red: #ec1f27;
    --card-red-top: #d8231f;
    --card-red-bottom: #c81e1c;
    --navy: #34495e;
    --ink: #333333;
    --muted: #555555;
    --card-white: #fbfbfb;
    --backdrop: #ebebeb;
  }
  * { margin: 0; padding: 0; box-sizing: border-box; }
  html, body {
    width: 1200px;
    height: 576px;
    overflow: hidden;
    background: var(--backdrop);
  }
  .canvas {
    position: relative;
    width: 1200px;
    height: 576px;
  }
  .card {
    position: absolute;
    top: 138px;
    width: 483px;
    height: 294px;
    border-radius: 7px;
    box-shadow: 0 2px 5px rgba(0, 0, 0, 0.22);
  }
  .card--front {
    left: 81px;
    background: linear-gradient(180deg, var(--card-red-top), var(--card-red-bottom));
  }
  .card--back {
    left: 602px;
    background: var(--card-white);
  }

  /* Wordmark */
  .wordmark {
    position: absolute;
    font-family: "Oswald", sans-serif;
    font-weight: 600;
    text-transform: uppercase;
    text-align: center;
    line-height: 1;
  }
  .wordmark__name { display: block; }
  .wordmark__sub { display: block; }

  .card--front .wordmark {
    left: 0;
    right: 0;
    top: 108px;
    color: #ffffff;
  }
  .card--front .wordmark__name { font-size: 46px; letter-spacing: 2px; }
  .card--front .wordmark__sub { font-size: 15px; letter-spacing: 3.5px; margin-top: 12px; }

  .card--back .wordmark {
    left: 22px;
    top: 30px;
    width: 220px;
    color: var(--navy);
  }
  .card--back .wordmark__name { font-size: 38px; letter-spacing: 1.5px; }
  .card--back .wordmark__sub { font-size: 12px; letter-spacing: 2.8px; margin-top: 10px; }

  /* Person */
  .person {
    position: absolute;
    left: 22px;
    top: 160px;
  }
  .person__name {
    font-family: "Oswald", sans-serif;
    font-weight: 400;
    font-size: 22px;
    color: var(--brand-red);
    line-height: 1.1;
  }
  .person__title {
    font-family: "Roboto", sans-serif;
    font-size: 12px;
    color: var(--muted);
    margin-top: 3px;
  }

  /* Services */
  .services {
    position: absolute;
    left: 22px;
    top: 230px;
    width: 200px;
    display: flex;
    flex-wrap: wrap;
    list-style: none;
    font-family: "Oswald", sans-serif;
    font-weight: 300;
    font-size: 12.5px;
    color: var(--ink);
    line-height: 16px;
    column-gap: 6px;
  }
  .services li::before { content: "» "; }

  /* Contacts */
  .contacts {
    position: absolute;
    left: 282px;
    top: 162px;
    list-style: none;
    font-family: "Oswald", sans-serif;
    font-weight: 300;
    font-size: 12.5px;
    color: var(--ink);
  }
  .contacts li {
    display: flex;
    align-items: center;
    height: 15.7px;
  }
  .contacts svg {
    width: 10px;
    height: 10px;
    margin-right: 8px;
    fill: var(--brand-red);
    flex: none;
  }
</style>
</head>
<body>
<main class="canvas">

  <section class="card card--front" aria-label="Card front">
    <div class="wordmark">
      <span class="wordmark__name">Brenwick</span>
      <span class="wordmark__sub">Casing Services</span>
    </div>
  </section>

  <section class="card card--back" aria-label="Card back">
    <div class="wordmark">
      <span class="wordmark__name">Brenwick</span>
      <span class="wordmark__sub">Casing Services</span>
    </div>

    <div class="person">
      <h1 class="person__name">Cody Hartwell</h1>
      <p class="person__title">Area Manager</p>
    </div>

    <ul class="services">
      <li>Laydown Machine</li>
      <li>Casing Crew</li>
      <li>Mud Tool</li>
      <li>Torque Turn</li>
    </ul>

    <ul class="contacts">
      <li>
        <svg viewBox="0 0 10 10" aria-hidden="true"><path d="M2 0.5 L3.6 2.6 L2.8 3.6 Q4 6 6.4 7.2 L7.4 6.4 L9.5 8 L8.2 9.5 Q4.5 9.5 2 7 Q0 4.5 0.5 1.8 Z"/></svg>
        <span>(555) 214-3800</span>
      </li>
      <li>
        <svg viewBox="0 0 10 10" aria-hidden="true"><path d="M0 3 Q5 0 10 3 L10 4.3 L7.5 4.3 L7.5 3.3 Q5 2.6 2.5 3.3 L2.5 4.3 L0 4.3 Z M2 5 L8 5 L9 9.5 L1 9.5 Z"/></svg>
        <span>(555) 387-6142</span>
      </li>
      <li>
        <svg viewBox="0 0 10 10" aria-hidden="true"><path d="M2.5 0.5 H7.5 V3 H2.5 Z M0.5 3.5 H9.5 V7.5 H8 V6 H2 V7.5 H0.5 Z M2.5 6.5 H7.5 V9.5 H2.5 Z"/></svg>
        <span>(555) 214-3811</span>
      </li>
      <li>
        <svg viewBox="0 0 10 10" aria-hidden="true"><path d="M5 0 A3.6 3.6 0 0 1 8.6 3.6 C8.6 6 5 10 5 10 C5 10 1.4 6 1.4 3.6 A3.6 3.6 0 0 1 5 0 Z M5 2.2 A1.4 1.4 0 1 0 5 5 A1.4 1.4 0 1 0 5 2.2 Z"/></svg>
        <span>Alder Springs, OK 73000</span>
      </li>
      <li>
        <svg viewBox="0 0 10 10" aria-hidden="true"><path d="M0.5 2 H9.5 L5 5.5 Z M0.5 3 L5 6.5 L9.5 3 V8.5 H0.5 Z"/></svg>
        <span>codyhartwell@brenwicksvc.com</span>
      </li>
      <li>
        <svg viewBox="0 0 10 10" aria-hidden="true"><path d="M5 0.5 A4.5 4.5 0 1 0 5 9.5 A4.5 4.5 0 1 0 5 0.5 Z M5 1.6 Q6.6 3.2 6.6 5 Q6.6 6.8 5 8.4 Q3.4 6.8 3.4 5 Q3.4 3.2 5 1.6 Z M1.5 4.6 H8.5 V5.4 H1.5 Z" fill-rule="evenodd"/></svg>
        <span>www.brenwicksvc.com</span>
      </li>
    </ul>
  </section>

</main>
</body>
</html>
```